Now Leasing Banner

Looking for a banner that says the following information approx 4' x 30'

Now Leasing Maplebrook Terrace 925-318-6042

Target Market(s)

Drive by traffic

Industry/Entity Type

Residential property management

Requirements
Must have
• Clear and readable from a distance

```html
<!DOCTYPE html>
<html lang="en">
<head>
<meta charset="utf-8">
<title>Now Leasing – Maplebrook Terrace Banners</title>
<link rel="stylesheet" href="https://fonts.googleapis.com/css2?family=Stint+Ultra+Condensed&display=swap">
<style>
  :root {
    --brand-red: #ed1c24;
    --brand-charcoal: #333333;
    --brand-yellow: #fff200;
    --brand-white: #ffffff;
    --stage-light: #eeeeee;
    --stage-dark: #858585;
  }
  html, body {
    margin: 0;
    padding: 0;
    width: 1200px;
    height: 675px;
    overflow: hidden;
  }
  .stage {
    width: 1200px;
    height: 675px;
    background: radial-gradient(ellipse at 50% 50%, var(--stage-light) 0%, var(--stage-dark) 85%);
  }
  .banner-set {
    display: block;
    width: 1200px;
    height: 675px;
  }
  .banner { filter: drop-shadow(0 6px 5px rgba(0, 0, 0, 0.28)); }
  .banner-text {
    font-family: "Stint Ultra Condensed", "Times New Roman", serif;
    text-transform: uppercase;
  }
  .fill-red { fill: var(--brand-red); }
  .fill-charcoal { fill: var(--brand-charcoal); }
  .fill-yellow { fill: var(--brand-yellow); }
  .fill-white { fill: var(--brand-white); }
</style>
</head>
<body>
<main class="stage">
  <svg class="banner-set" viewBox="0 0 1366 768" xmlns="http://www.w3.org/2000/svg" aria-label="Three Now Leasing banner options for Maplebrook Terrace">

    <!-- Option 1: red headline panel with white contact panel -->
    <g class="banner banner--red-headline">
      <rect class="fill-white" x="153" y="96" width="1060" height="141"/>
      <polygon class="fill-red" points="153,96 826,96 858,166 826,237 153,237"/>
      <text class="banner-text fill-white" x="170" y="221" font-size="150" textLength="638" lengthAdjust="spacingAndGlyphs">Now Leasing</text>
      <text class="banner-text fill-red" x="862" y="160" font-size="68" textLength="333" lengthAdjust="spacingAndGlyphs">Maplebrook Terrace</text>
      <text class="banner-text fill-charcoal" x="862" y="225" font-size="80" textLength="331" lengthAdjust="spacingAndGlyphs">925-318-6042</text>
    </g>

    <!-- Option 2: charcoal name panel with red phone panel -->
    <g class="banner banner--phone-focus">
      <rect class="fill-red" x="153" y="314" width="1060" height="141"/>
      <polygon class="fill-charcoal" points="153,314 560,314 583,385 560,455 153,455"/>
      <text class="banner-text fill-white" x="178" y="430" font-size="134" textLength="179" lengthAdjust="spacingAndGlyphs">Now</text>
      <text class="banner-text fill-yellow" x="364" y="392" font-size="78" textLength="191" lengthAdjust="spacingAndGlyphs">Leasing</text>
      <text class="banner-text fill-white" x="364" y="431" font-size="38" textLength="189" lengthAdjust="spacingAndGlyphs">Maplebrook Terrace</text>
      <text class="banner-text fill-white" x="601" y="427" font-size="134" textLength="565" lengthAdjust="spacingAndGlyphs">925-318-6042</text>
    </g>

    <!-- Option 3: white headline panel with red contact panel -->
    <g class="banner banner--white-headline">
      <rect class="fill-white" x="153" y="539" width="1060" height="141"/>
      <rect class="fill-red" x="848" y="539" width="365" height="141"/>
      <text class="banner-text fill-red" x="178" y="668" font-size="168" textLength="215" lengthAdjust="spacingAndGlyphs">Now</text>
      <text class="banner-text fill-charcoal" x="427" y="668" font-size="168" textLength="398" lengthAdjust="spacingAndGlyphs">Leasing</text>
      <text class="banner-text fill-white" x="870" y="602" font-size="66" textLength="317" lengthAdjust="spacingAndGlyphs">Maplebrook Terrace</text>
      <text class="banner-text fill-white" x="870" y="668" font-size="78" textLength="315" lengthAdjust="spacingAndGlyphs">925-318-6042</text>
    </g>
  </svg>
</main>
</body>
</html>
```